Label design

Description
I want you to design a label for a skin care product line. I’ve provide the picture of the jar we are using along with the logo. Please note that the logo is available in different colors as well. (See attached) I would like the label to be very clean and straight to the point. Here is some info that I would like to see on the label:
240G
Net wt 8.0z

The content of the jar can be refer to as:

Body cream
Crème de corps
Body butter
Fade cream
Skin tone cream
Lotion pour le corps
Clarifying Body cream
Lightening Cream

The content is also made an exotic component that: “Extraits de noisette de palmiers” meaning nuts extract.

The brand NAME is: Mirevo
The tag line is: Be yourself, love yourself

Industry/Entity Type

Skin Care Product

```html
<!DOCTYPE html>
<html lang="en">
<head>
<meta charset="utf-8">
<title>Mirevo Baby Lotion Label</title>
<link rel="stylesheet" href="https://fonts.googleapis.com/css2?family=Quicksand:wght@400;500&display=swap">
<style>
  :root {
    --page-bg: #ffffff;
    --label-light: #f7f7f7;
    --label-mid: #ebebec;
    --label-dark: #c4c5c7;
    --brand-pink: #ec5a78;
    --soft-pink: #f07a90;
  }
  html, body {
    margin: 0;
    padding: 0;
    width: 1200px;
    height: 1200px;
    overflow: hidden;
    background: var(--page-bg);
  }
  .canvas {
    position: relative;
    width: 1200px;
    height: 1200px;
    font-family: "Quicksand", sans-serif;
  }
  .label {
    position: absolute;
    left: 130px;
    top: 276px;
    width: 940px;
    height: 648px;
    border-radius: 14px;
    overflow: hidden;
    background: linear-gradient(90deg, var(--label-mid) 0%, var(--label-light) 30%, var(--label-mid) 65%, var(--label-dark) 100%);
  }
  .brand-name {
    position: absolute;
    left: 0;
    right: 0;
    top: 232px;
    margin: 0;
    text-align: center;
    font-size: 104px;
    font-weight: 400;
    line-height: 1;
    color: var(--brand-pink);
    letter-spacing: 1px;
  }
  .tagline {
    position: absolute;
    left: 0;
    right: 0;
    top: 360px;
    margin: 0;
    text-align: center;
    font-size: 25px;
    font-weight: 500;
    color: var(--brand-pink);
  }
  .product-name {
    position: absolute;
    left: 0;
    right: 0;
    top: 440px;
    margin: 0;
    text-align: center;
    font-size: 54px;
    font-weight: 400;
    color: var(--brand-pink);
  }
  .ingredient {
    position: absolute;
    left: 0;
    right: 0;
    top: 508px;
    margin: 0;
    text-align: center;
    font-size: 23px;
    font-weight: 400;
    color: var(--soft-pink);
  }
  .net-weight,
  .gram-weight {
    position: absolute;
    top: 571px;
    margin: 0;
    font-size: 24px;
    font-weight: 400;
    color: var(--brand-pink);
  }
  .net-weight { left: 24px; }
  .gram-weight { right: 28px; }
  .border-band {
    position: absolute;
    left: 0;
    right: 0;
    bottom: 0;
    height: 30px;
    background: var(--brand-pink);
  }
</style>
</head>
<body>
  <main class="canvas">
    <section class="label">
      <h1 class="brand-name">Mirevo</h1>
      <p class="tagline">Be yourself, love yourself</p>
      <h2 class="product-name">Baby lotion</h2>
      <p class="ingredient">Extraits de noisette de palmiers</p>
      <p class="net-weight">Net wt 8.0z</p>
      <p class="gram-weight">240g</p>
      <div class="border-band" role="img" aria-label="Row of pink dots forming a scalloped border along the bottom edge"></div>
    </section>
  </main>
</body>
</html>
```